Flat bootstrap design for existing site

I'm looking for a modern flat design based around an existing logo. This has to be a custom design (no external templates), and implemented into a bootstrap framework.

The logo is attached as 2 versions - choose whichever you want, that flows better with whatever design you choose.

Added screenshots of the existing site (currently using the default bootstrap layouts). Please make your designs around those pages in the screenshots (i.e. the homepage only has the postal code input and the header). The active page has 3 screenshots, because I wanted to illustrate the other states that would be visible (in the table rows).

This is a moving/junk removal website, just for some context.

Here's some example websites (flat designs) that I like, just to give you an idea of what I'm after.

https://www.plimvora.com/
https://dacklow.com/
https://trevanu.com/
https://quobrintal.com/en/

Coding

Coded - Design and coding required

Number of Pages Required

5+ page

Colors

Designer to choose colors to be used in the design.

Requirements
Must have
• It must be a modern/simple flat design, that is built around the existing logo (attached).
• It has to be implemented using bootstrap.

```html
<!DOCTYPE html>
<html lang="en">
<head>
<meta charset="utf-8">
<title>Halvery – Sign in</title>
<link rel="stylesheet" href="https://fonts.googleapis.com/css2?family=Raleway:wght@400;500;600;700&display=swap">
<style>
  :root {
    --sky: #56cdf5;
    --sky-deep: #45c5f2;
    --white: #ffffff;
    --ink: #2b2b2b;
    --field-border: #e3e3e3;
    --placeholder: #7a7a7a;
    --button: #3e7bb4;
  }
  * { box-sizing: border-box; margin: 0; padding: 0; }
  html, body {
    width: 1200px; height: 760px; overflow: hidden;
    background: var(--white);
    font-family: "Raleway", sans-serif;
  }
  .page { position: relative; width: 1200px; height: 760px; }

  .site-header {
    position: absolute; top: 0; left: 0; width: 1200px; height: 75px;
    background: linear-gradient(90deg, var(--sky), var(--sky-deep));
  }
  .brand {
    position: absolute; left: 100px; top: 0; height: 75px;
    display: flex; align-items: center; gap: 8px;
    color: var(--white); font-weight: 700; font-size: 30px; letter-spacing: 1px;
  }
  .brand-dot { width: 14px; height: 14px; border-radius: 50%; background: var(--white); }
  .main-nav { position: absolute; right: 0; top: 0; height: 75px; display: flex; }
  .main-nav a {
    display: flex; align-items: center; height: 75px; padding: 0 22px;
    color: var(--white); text-decoration: none; font-size: 13.5px; font-weight: 500;
  }
  .main-nav .nav-book { margin-right: 0; }
  .main-nav .nav-current { background: var(--white); color: var(--sky-deep); }
  .main-nav .nav-signin { padding-right: 100px; }

  .signin {
    position: absolute; left: 430px; top: 140px; width: 340px;
  }
  .signin-title { font-size: 33px; font-weight: 500; color: var(--ink); line-height: 1; }
  .signin-form { margin-top: 41px; margin-left: 3px; width: 335px; }
  .field {
    display: block; width: 335px; height: 48px; margin-bottom: 9px;
    border: 1px solid var(--field-border); background: var(--white);
    padding: 0 17px; font-family: inherit; font-size: 13px; color: var(--ink);
  }
  .field::placeholder { color: var(--placeholder); }
  .login-button {
    display: block; width: 335px; height: 49px; border: none;
    background: var(--button); color: var(--white);
    font-family: inherit; font-weight: 700; font-size: 14px; letter-spacing: 2px;
  }

  .site-footer {
    position: absolute; left: 0; bottom: 0; width: 1200px; height: 47px;
    background: linear-gradient(90deg, var(--sky), var(--sky-deep));
    display: flex; align-items: center; justify-content: center;
    color: var(--white); font-size: 12.5px;
  }
</style>
</head>
<body>
<div class="page">
  <header class="site-header">
    <div class="brand"><span class="brand-dot"></span>HALVERY</div>
    <nav class="main-nav">
      <a href="#" class="nav-book">BOOK</a>
      <a href="#">HOW IT WORKS</a>
      <a href="#" class="nav-current">BECOME A DRIVER</a>
      <a href="#" class="nav-signin">SIGN IN</a>
    </nav>
  </header>

  <main class="signin">
    <h1 class="signin-title">Please Sign in</h1>
    <form class="signin-form">
      <input class="field" type="email" placeholder="Email Address">
      <input class="field" type="password" placeholder="Password">
      <button class="login-button" type="button">LOG IN</button>
    </form>
  </main>

  <footer class="site-footer">© copyright 2017 Halvery.All Rights Reserved</footer>
</div>
</body>
</html>
```